Stylish Business Cards Wanted

- DOUBLE SIDED Design Required -

High end, edgy cards for a corporate and personal stylist. Must include logo,
Name: Belinda Harwick
Title: Director and Stylist
telephone : +61 8 7142 5809
email: belinda@theloombriefing.example
website: theloombriefing.example
Tag: Corporate Workwear & Uniform Specialist | Personal Stylist
Would like nice icons for telephone, email, website

Target Market(s)

Businesses wanting stylish uniforms, people wanting stylish wardrobes

Industry/Entity Type

Corporate Workwear Stylist

Contact Information for Business Card

I would like black, white and gold foiling incorporated in the design - possibly a touch of the other colours on my branding guide attached Name: Belinda Harwick Title: Director and Stylist telephone : +61 8 7142 5809 email: belinda@theloombriefing.example website: theloombriefing.example Tag: Corporate Workwear & Uniform Specialist | Personal Stylist Would like nice icons for telephone, email, website

Font styles to use
Other font styles liked:
• Raleway

Colors

Designer to choose colors to be used in the design.

Requirements
Must have
• Gold foil accents

```html
<!DOCTYPE html>
<html lang="en">
<head>
<meta charset="utf-8">
<title>The Loom Briefing — Business Cards</title>
<link rel="stylesheet" href="https://fonts.googleapis.com/css2?family=Montserrat:wght@400;500&family=Raleway:wght@400;500;600&display=swap">
<style>
  :root {
    --backdrop: #d9d9d9;
    --card-black: #1f1d1e;
    --foil-gold: #d9aa2c;
    --foil-edge: #e0b437;
    --ink-white: #f2f2f2;
    --ink-soft: #cfcfcf;
    --divider: #3a3839;
  }
  * { margin: 0; padding: 0; box-sizing: border-box; }
  html, body {
    width: 1200px;
    height: 800px;
    overflow: hidden;
    background: var(--backdrop);
  }
  .canvas {
    width: 1200px;
    height: 800px;
    display: flex;
    align-items: center;
    justify-content: center;
    gap: 40px;
  }
  .card {
    width: 560px;
    height: 342px;
    background: var(--card-black);
    border: 2px solid var(--foil-edge);
    position: relative;
    overflow: hidden;
  }

  /* Contact side */
  .card--contact {
    display: flex;
    align-items: center;
  }
  .brand-block {
    width: 230px;
    display: flex;
    justify-content: center;
  }
  .brand-name {
    font-family: "Raleway", sans-serif;
    font-weight: 600;
    line-height: 1.15;
    text-align: center;
  }
  .brand-name--white {
    color: var(--ink-white);
    font-size: 26px;
  }
  .divider {
    width: 1px;
    height: 150px;
    background: var(--divider);
  }
  .contact-block {
    padding-left: 30px;
  }
  .person-name {
    font-family: "Montserrat", sans-serif;
    font-weight: 500;
    font-size: 21px;
    letter-spacing: 0.5px;
    color: var(--ink-white);
    text-transform: uppercase;
  }
  .person-title {
    font-family: "Raleway", sans-serif;
    font-size: 15px;
    color: var(--foil-gold);
    margin-top: 2px;
    margin-bottom: 18px;
  }
  .contact-list {
    list-style: none;
  }
  .contact-item {
    display: flex;
    align-items: center;
    gap: 10px;
    font-family: "Raleway", sans-serif;
    font-size: 13px;
    color: var(--ink-soft);
    margin-bottom: 7px;
  }
  .contact-icon {
    width: 14px;
    height: 14px;
    flex: none;
  }

  /* Brand side */
  .card--brand {
    display: flex;
    flex-direction: column;
    align-items: center;
    justify-content: center;
  }
  .brand-lockup {
    display: flex;
    align-items: center;
    gap: 14px;
    margin-top: -20px;
  }
  .brand-mark {
    width: 14px;
    height: 14px;
    border-radius: 50%;
    background: var(--foil-gold);
  }
  .brand-name--gold {
    color: var(--foil-gold);
    font-size: 40px;
  }
  .tagline {
    position: absolute;
    bottom: 34px;
    left: 0;
    right: 0;
    text-align: center;
    font-family: "Montserrat", sans-serif;
    font-size: 11.5px;
    letter-spacing: 1.2px;
    color: var(--ink-soft);
    text-transform: uppercase;
  }
  .tagline-sep {
    color: var(--foil-gold);
    margin: 0 5px;
  }
</style>
</head>
<body>
<main class="canvas">

  <section class="card card--contact" aria-label="Business card, contact side">
    <div class="brand-block">
      <p class="brand-name brand-name--white">The Loom<br>Briefing</p>
    </div>
    <div class="divider"></div>
    <div class="contact-block">
      <h1 class="person-name">Belinda Harwick</h1>
      <p class="person-title">Director &amp; Stylist</p>
      <ul class="contact-list">
        <li class="contact-item">
          <svg class="contact-icon" viewBox="0 0 24 24" aria-hidden="true">
            <path fill="#d9aa2c" d="M6.6 10.8a15.1 15.1 0 0 0 6.6 6.6l2.2-2.2a1 1 0 0 1 1-.25 11.4 11.4 0 0 0 3.6.57 1 1 0 0 1 1 1V20a1 1 0 0 1-1 1A17 17 0 0 1 3 4a1 1 0 0 1 1-1h3.5a1 1 0 0 1 1 1c0 1.25.2 2.45.57 3.57a1 1 0 0 1-.25 1z"/>
          </svg>
          <span>+61 8 7142 5809</span>
        </li>
        <li class="contact-item">
          <svg class="contact-icon" viewBox="0 0 24 24" aria-hidden="true">
            <rect x="2" y="5" width="20" height="14" rx="1.5" fill="#d9aa2c"/>
            <path d="M3 6.5l9 6.5 9-6.5" fill="none" stroke="#1f1d1e" stroke-width="1.8"/>
          </svg>
          <span>belinda@theloombriefing.example</span>
        </li>
        <li class="contact-item">
          <svg class="contact-icon" viewBox="0 0 24 24" aria-hidden="true">
            <circle cx="12" cy="12" r="10" fill="#d9aa2c"/>
            <g fill="none" stroke="#1f1d1e" stroke-width="1.4">
              <ellipse cx="12" cy="12" rx="4" ry="10"/>
              <path d="M2 12h20M4 7h16M4 17h16"/>
            </g>
          </svg>
          <span>theloombriefing.example</span>
        </li>
      </ul>
    </div>
  </section>

  <section class="card card--brand" aria-label="Business card, brand side">
    <div class="brand-lockup">
      <span class="brand-mark" aria-hidden="true"></span>
      <p class="brand-name brand-name--gold">The Loom Briefing</p>
    </div>
    <p class="tagline">
      Corporate Workwear<span class="tagline-sep">|</span>Uniform Specialist<span class="tagline-sep">|</span>Personal Stylist
    </p>
  </section>

</main>
</body>
</html>
```